Redesign Merle's RV Park & Lodge Website, Leeds, North Dakota

I need a totally re-designed website for my RV Park / Lodge. I want to not only provide information on my RV Park / Lodge, I want to provide my customers with information on the town and area attractions. I want to provide rate information. Ideally, I would like to have a button/page for each section: Welcome & Information, Area Attractions, Welcome to Leeds, Rates, Who's Merle?!, FAQ's and Where are we?. I don't know if this would be more expensive the more pages you have? If more pages is too expensive, then we can combine info on less pages. I want my logo included on the web page. I want Studio Flock to take down my old website and use the same address to put up my newly designed website.

Target Market(s)

Full time RVers, People who camp, hunt fish, People who recreate on Devils Lake, People who are looking for meeting/conference space, people who are looking for party venue

Industry/Entity Type

Accommodation

Number of Pages Required

3 page

Requirements
Must have
• I want a cozy, welcoming type web site. No super dark colors. Bright and cheerful.
• Must be simple and organized.
• NOTE: I have a file of pictures of the interior of Merle's Lodge that must be included in website. Please request this file if you will be designing my project as the files are too large to upload through Studio Flock.
Nice to have
• If you cannot open any of the files listed, please notify me.
Should not have
• No stark or super-formal designs.

```html
<!DOCTYPE html>
<html lang="en">
<head>
<meta charset="utf-8">
<title>Merle's RV Park &amp; Lodge</title>
<link href="https://fonts.googleapis.com/css2?family=Playfair+Display:wght@400;700&family=Lato:wght@400;700&display=swap" rel="stylesheet">
<style>
:root{
  --green:#4c5a2a;
  --green-dark:#3d4a22;
  --maroon:#6b1a24;
  --maroon-deep:#5a1019;
  --text:#555;
  --muted:#777;
  --light:#f5f5f3;
  --white:#fff;
  --line:#ddd;
  --ink:#222;
}
*{margin:0;padding:0;box-sizing:border-box}
html,body{width:1200px;height:3586px;overflow:hidden}
body{font-family:"Lato",sans-serif;color:var(--text);background:var(--white);position:relative}
.abs{position:absolute}
.serif{font-family:"Playfair Display",serif}
section,header,footer{position:absolute;left:0;width:1200px}

/* hero */
.hero{top:0;height:464px;background:linear-gradient(180deg,#b9c9d6 0%,#d8dde0 30%,#a9a49a 55%,#6d8a3c 75%,#8c9a55 100%)}
.hero::after{content:"";position:absolute;inset:0;background:rgba(0,0,0,.15)}
.nav{position:absolute;top:0;left:0;width:1200px;height:56px;background:rgba(107,26,36,.75);z-index:2;display:flex;justify-content:flex-end;align-items:center;padding-right:60px;gap:36px}
.nav a{color:var(--white);font-size:13px;font-weight:700;text-decoration:none;white-space:nowrap}
.badge{position:absolute;left:78px;top:0;width:108px;height:142px;background:var(--white);z-index:3;clip-path:polygon(0 0,100% 0,100% 84%,50% 100%,0 84%);display:flex;flex-direction:column;align-items:center;padding-top:30px}
.badge .mark{width:16px;height:16px;background:var(--maroon);margin-bottom:8px}
.badge span{font-family:"Playfair Display",serif;font-weight:700;font-size:12px;color:var(--ink);text-align:center;line-height:1.2}
.hero h1{position:absolute;top:208px;width:100%;text-align:center;z-index:2;font-family:"Playfair Display",serif;font-size:52px;line-height:1.2;color:var(--white);font-weight:400}
.btn{display:inline-block;background:var(--maroon);color:var(--white);border-radius:22px;font-size:14px;text-align:center;text-decoration:none}
.hero .btn{position:absolute;left:525px;top:316px;width:150px;height:40px;line-height:40px;z-index:2}
.dots{position:absolute;top:434px;left:574px;z-index:2;display:flex;gap:9px}
.dots i{width:9px;height:9px;border-radius:50%;background:var(--white);opacity:.7}
.dots i:nth-child(2){opacity:1}

/* welcome */
.welcome{top:464px;height:504px;background:var(--light);border-bottom:1px solid var(--line)}
.portrait{left:120px;top:56px;width:401px;height:375px;background:linear-gradient(160deg,#e8e4de,#c9b79a 55%,#5f6b4a);box-shadow:0 10px 24px rgba(0,0,0,.25)}
.welcome h2{left:588px;top:120px;font-size:28px;color:var(--green);font-weight:400}
.welcome .sub{left:588px;top:160px;font-size:15px;color:var(--ink);font-family:"Playfair Display",serif;font-weight:700}
.welcome hr{position:absolute;left:588px;top:192px;width:490px;border:0;border-top:1px solid #ccc}
.welcome p{left:588px;top:212px;width:490px;font-size:14px;line-height:1.75}
.welcome .btn{left:588px;top:307px;width:156px;height:42px;line-height:42px}

/* features */
.block-title{width:100%;text-align:center;font-family:"Playfair Display",serif;font-weight:700;font-size:28px;color:var(--green)}
.intro{left:100px;width:1000px;text-align:center;font-size:13.5px;line-height:1.75;color:var(--muted)}
.panel{left:53px;width:1094px;color:var(--white)}
.panel h3{position:absolute;top:28px;width:100%;text-align:center;font-family:"Playfair Display",serif;font-size:28px;font-weight:700}
.cols{position:absolute;top:112px;left:28px;right:28px;display:grid;grid-template-columns:1fr 1fr 1fr;gap:30px}
.cols ul{list-style:none}
.cols li{position:relative;padding-left:30px;font-size:13.5px;line-height:1.75;margin-bottom:2px}
.cols li svg{position:absolute;left:4px;top:6px}

.lodge{top:968px;height:652px;background:var(--white);border-bottom:1px solid var(--line)}
.lodge .block-title{position:absolute;top:60px}
.lodge .intro{top:120px}
.lodge .panel{top:260px;height:311px;background:linear-gradient(135deg,rgba(76,90,42,.92),rgba(86,102,50,.9))}

.rv{top:1620px;height:686px;background:var(--light)}
.rv .block-title{position:absolute;top:62px}
.rv .intro{top:125px;color:var(--text)}
.rv .panel{left:67px;width:1080px;top:287px;height:311px;background:linear-gradient(135deg,rgba(107,26,36,.95),rgba(120,34,46,.92))}

/* rates */
.rates{top:2306px;height:889px;background:var(--light)}
.rates-photo{left:0;top:0;width:562px;height:889px;background:linear-gradient(160deg,#2b3318,#3f4c22 45%,#263012)}
.rates-photo h2{position:absolute;left:58px;top:340px;font-family:"Playfair Display",serif;color:var(--white);font-size:48px;line-height:1.1;font-weight:400}
.rates-photo .r{position:absolute;left:58px;top:462px;color:var(--white);font-size:34px;font-family:"Playfair Display",serif}
.rates-photo .btn{position:absolute;left:58px;top:538px;width:206px;height:48px;line-height:48px;font-size:24px}
.label{left:614px;font-family:"Playfair Display",serif;font-weight:700;font-size:14px;color:var(--green)}
.price-h{left:614px;font-family:"Playfair Display",serif;color:var(--maroon);font-size:38px}
.price-h small{font-size:28px}
.rate-row{left:614px;font-family:"Playfair Display",serif;color:var(--maroon);font-size:38px;font-weight:700}
.rate-row span{font-size:12px;font-weight:400;margin-right:16px}
.note{left:614px;width:420px;font-size:13px;line-height:1.7;color:var(--muted)}
.rule{left:614px;width:380px;border-top:1px solid #ccc}
.sub-h{left:608px;font-family:"Playfair Display",serif;color:var(--ink);font-size:32px}

/* footer */
.site-footer{top:3195px;height:337px;background:var(--light);border-top:1px solid var(--line)}
.f-logo{left:88px;top:62px;width:104px;text-align:center}
.f-logo .mark{width:16px;height:16px;background:var(--maroon);margin:0 auto 8px}
.f-logo span{font-family:"Playfair Display",serif;font-weight:700;font-size:13px;color:var(--ink);line-height:1.25}
.f-head{font-weight:700;font-size:13px;color:var(--maroon)}
.f-list{list-style:none;font-size:13px;color:var(--ink);line-height:1.6}
.contact{left:478px;top:74px}
.contact .row{position:relative;padding-left:38px;font-size:12.5px;color:var(--ink);line-height:1.6;margin-top:14px}
.contact .row svg{position:absolute;left:0;top:3px}
.map{left:793px;top:110px;width:354px;height:117px;background:linear-gradient(135deg,#f1efe6,#e2e6d6 50%,#d9e2ea);border:1px solid #ccc}
.bottom{top:3532px;height:54px;background:var(--white);border-top:1px solid var(--line);text-align:center;line-height:54px;font-size:13px;color:var(--ink);font-weight:700}
</style>
</head>
<body>

<header class="hero" role="img" aria-label="Photo of the lodge building with red roof and open-sided patio on a green lawn">
  <nav class="nav">
    <a href="#">Home</a><a href="#">Welcome &amp; Information</a><a href="#">Area Attractions</a><a href="#">Welcome to Leeds</a><a href="#">Rates</a><a href="#">Who's Merle?!</a><a href="#">FAQ's</a><a href="#">Where Are We</a>
  </nav>
  <div class="badge"><div class="mark"></div><span>Merle's RV Park<br>&amp; Lodge<br>Leeds ND</span></div>
  <h1>Merle RV Park &amp; Lodge</h1>
  <a class="btn" href="#">Learn More</a>
  <div class="dots"><i></i><i></i><i></i><i></i></div>
</header>

<section class="welcome">
  <div class="abs portrait" role="img" aria-label="Portrait photo of the owner Merle"></div>
  <h2 class="abs serif">Welcome to Merle's RV Park &amp; Lodge</h2>
  <div class="abs sub">Leeds, North Dakota</div>
  <hr>
  <p class="abs">Leeds is in the heart of some of the greatest hunting and fishing in the world. Merle&amp; RV Park is located right on Highway 2 midway between Devils Lake and Rugby North Dakota. We are smack dab in the middle of it all!</p>
  <a class="abs btn" href="#">Read More</a>
</section>

<section class="lodge">
  <h2 class="block-title">Merle's Lodge</h2>
  <p class="abs intro">Are you looking for a cozy, but spacious home away from home? Well, you have found it! Merle's Lodge is 2200 square feet of living space. There are 2 spacious bedrooms with queen sized beds and another common sleeping area with 5 sets of bunk beds. Available to you are 2 restrooms with showers, a great room with dining and relaxing space and a full kitchen.Everything is supplied for you: towels, bedding, cookware, dishware, grill and etc...all that you need to make your stay worry and hassle free. Throw some clothes in a suitcase, hit the road and we will have your home away from home all ready when you get here! The Lodge is open all year round.</p>
  <div class="abs panel" role="img" aria-label="Faded photo of the lodge great room with dining tables">
    <h3>Merle's Lodge</h3>
    <div class="cols">
      <ul>
        <li><svg width="12" height="10" viewBox="0 0 12 10"><path d="M1 5l3.5 3.5L11 1" stroke="#fff" stroke-width="2" fill="none"/></svg>Groups – hunting, fishing, working, playing</li>
        <li><svg width="12" height="10" viewBox="0 0 12 10"><path d="M1 5l3.5 3.5L11 1" stroke="#fff" stroke-width="2" fill="none"/></svg>2200 square feet</li>
        <li><svg width="12" height="10" viewBox="0 0 12 10"><path d="M1 5l3.5 3.5L11 1" stroke="#fff" stroke-width="2" fill="none"/></svg>Full kitchen</li>
        <li><svg width="12" height="10" viewBox="0 0 12 10"><path d="M1 5l3.5 3.5L11 1" stroke="#fff" stroke-width="2" fill="none"/></svg>Free WiFi</li>
      </ul>
      <ul>
        <li><svg width="12" height="10" viewBox="0 0 12 10"><path d="M1 5l3.5 3.5L11 1" stroke="#fff" stroke-width="2" fill="none"/></svg>Satellite TV</li>
        <li><svg width="12" height="10" viewBox="0 0 12 10"><path d="M1 5l3.5 3.5L11 1" stroke="#fff" stroke-width="2" fill="none"/></svg>2 restrooms, one is handicap accessible</li>
        <li><svg width="12" height="10" viewBox="0 0 12 10"><path d="M1 5l3.5 3.5L11 1" stroke="#fff" stroke-width="2" fill="none"/></svg>Sleeps 14 – 2 bedrooms with queen sized beds, plus a shared sleeping area with bunk beds</li>
        <li><svg width="12" height="10" viewBox="0 0 12 10"><path d="M1 5l3.5 3.5L11 1" stroke="#fff" stroke-width="2" fill="none"/></svg>A great room with ample seating for large groups</li>
      </ul>
      <ul>
        <li><svg width="12" height="10" viewBox="0 0 12 10"><path d="M1 5l3.5 3.5L11 1" stroke="#fff" stroke-width="2" fill="none"/></svg>Merle supplies everything...bedding, towels, cookware, etc.</li>
        <li><svg width="12" height="10" viewBox="0 0 12 10"><path d="M1 5l3.5 3.5L11 1" stroke="#fff" stroke-width="2" fill="none"/></svg>Kids stay free.</li>
      </ul>
    </div>
  </div>
</section>

<section class="rv">
  <h2 class="block-title">Merle's RV Park</h2>
  <p class="abs intro">Merle's RV Park sits right next to Highway 2 on the north side. We have 14 full service spaces sewer, water and electric (20, 30, 50 amp). There is an indoor restroom with shower that is available 24 hours a day to our RV customers. Plenty of space is available to you for parking boats, trailers, etc.Merle&amp;#39;s RV Park year round, but water usage depends on when spring thaw and freeze up occurs.Please note: Merle's RV Park is an unattended RV park. No reservations required. Please pull onin, use our self-service check-in and then sit back and relax!</p>
  <div class="abs panel" role="img" aria-label="Faded photo of RV sites beside the park building">
    <h3>Merle's RV Park</h3>
    <div class="cols">
      <ul>
        <li><svg width="12" height="10" viewBox="0 0 12 10"><path d="M1 5l3.5 3.5L11 1" stroke="#fff" stroke-width="2" fill="none"/></svg>14 Full Service Sites</li>
        <li><svg width="12" height="10" viewBox="0 0 12 10"><path d="M1 5l3.5 3.5L11 1" stroke="#fff" stroke-width="2" fill="none"/></svg>Electric (23, 30 &amp; 50amp), Water, Sewer</li>
        <li><svg width="12" height="10" viewBox="0 0 12 10"><path d="M1 5l3.5 3.5L11 1" stroke="#fff" stroke-width="2" fill="none"/></svg>Free WiFi</li>
      </ul>
      <ul>
        <li><svg width="12" height="10" viewBox="0 0 12 10"><path d="M1 5l3.5 3.5L11 1" stroke="#fff" stroke-width="2" fill="none"/></svg>Safe &amp; convenient location</li>
        <li><svg width="12" height="10" viewBox="0 0 12 10"><path d="M1 5l3.5 3.5L11 1" stroke="#fff" stroke-width="2" fill="none"/></svg>24 hour indoor restroom with shower</li>
        <li><svg width="12" height="10" viewBox="0 0 12 10"><path d="M1 5l3.5 3.5L11 1" stroke="#fff" stroke-width="2" fill="none"/></svg>Roamers Club accepted for first night</li>
      </ul>
      <ul>
        <li><svg width="12" height="10" viewBox="0 0 12 10"><path d="M1 5l3.5 3.5L11 1" stroke="#fff" stroke-width="2" fill="none"/></svg>Ample room to park boats, trailers etc.</li>
        <li><svg width="12" height="10" viewBox="0 0 12 10"><path d="M1 5l3.5 3.5L11 1" stroke="#fff" stroke-width="2" fill="none"/></svg>Convenience store/gas station located right across the street. Restaurant onsite.</li>
        <li><svg width="12" height="10" viewBox="0 0 12 10"><path d="M1 5l3.5 3.5L11 1" stroke="#fff" stroke-width="2" fill="none"/></svg>Merle operates on a first come, first serve basis for short term stays. If you would like to reserve for a stay longer than 3 days, please call Merle.</li>
      </ul>
    </div>
  </div>
</section>

<section class="rates">
  <div class="abs rates-photo" role="img" aria-label="Dark green toned photo of a person seated on a large tractor">
    <h2>Merle RV Park<br>&amp; Logde</h2>
    <div class="r">Rates</div>
    <a class="btn" href="#">Click Here</a>
  </div>
  <div class="abs label" style="top:52px">Merle's Lodge Pricing</div>
  <div class="abs price-h" style="top:86px"><b>$200</b> <small>for 24 hours.</small></div>
  <p class="abs note" style="top:150px">The first 6 adults are included in the $200 per night rent.<br>Each adult exceeding the initial 6, must pay $25 per night.<br>Kids under age 16 stay free.</p>
  <div class="abs rule" style="top:256px"></div>
  <div class="abs label" style="top:290px">Merle's Lodge Pricing</div>
  <div class="abs sub-h" style="top:322px">RV Sites</div>
  <div class="abs rate-row" style="top:362px">$24<span>/Night</span>$125<span>/Week</span>$375<span>/month</span></div>
  <p class="abs note" style="top:430px">This price is for 4 adults. Any adults exceeding the initial 4, must pay<br>$5 extra per night. Kids under 16 stay free.</p>
  <div class="abs sub-h" style="top:515px">RV Sites</div>
  <div class="abs rate-row" style="top:555px">$24<span>/Night</span>$125<span>/Week</span>$375<span>/month</span></div>
  <p class="abs note" style="top:624px">This price is for 4 adults. Any adults exceeding the initial 4, must pay<br>$5 extra per night. Kids under 16 stay free.</p>
  <div class="abs rule" style="top:682px"></div>
  <div class="abs sub-h" style="top:700px">Showers</div>
  <div class="abs rate-row" style="top:744px;font-size:32px">$5<span>/Person</span></div>
  <p class="abs note" style="top:794px">For unregistered customers. There is no charge for anyone that uses the<br>shower that is staying at Merle's RV Park &amp; Lodge.</p>
</section>

<footer class="site-footer">
  <div class="abs f-logo"><div class="mark"></div><span>Merle's RV Park<br>&amp; Lodge<br>Leeds ND</span></div>
  <div class="abs" style="left:263px;top:74px">
    <div class="f-head">Menu Links</div>
    <ul class="f-list" style="margin-top:22px">
      <li>Home</li><li>Welcome &amp; Information</li><li>Area Attractions</li><li>Welcome to Leeds</li><li>Rates</li><li>Who's Merle?!</li><li>FAQ's</li><li>Where Are We</li>
    </ul>
  </div>
  <div class="abs contact">
    <div class="f-head">Contact Us</div>
    <div class="row" style="margin-top:22px"><svg width="12" height="16" viewBox="0 0 12 16"><path d="M6 0a6 6 0 0 0-6 6c0 4.5 6 10 6 10s6-5.5 6-10a6 6 0 0 0-6-6zm0 8.5A2.5 2.5 0 1 1 6 3.5a2.5 2.5 0 0 1 0 5z" fill="#333"/></svg><b>Dorothy Halvorsen</b><br>Merle's Trail Stop &amp; RV Park<br>214 Prairie Row NE | Leeds ND 58346</div>
    <div class="row"><svg width="14" height="14" viewBox="0 0 14 14"><path d="M3 0l3 3-2 2c1 2 3 4 5 5l2-2 3 3-2 3C6 14 0 8 0 2z" fill="#333"/></svg>701-555-0142<br>701-555-0187</div>
    <div class="row"><svg width="14" height="10" viewBox="0 0 14 10"><rect width="14" height="10" fill="#333"/><path d="M0 0l7 5 7-5" stroke="#fff" fill="none"/></svg>http://www.merlestrailstop.example/</div>
  </div>
  <div class="abs f-head" style="left:789px;top:74px">Locate Us</div>
  <div class="abs map" role="img" aria-label="Road map of the Leeds and Devils Lake area with a location marker"></div>
</footer>

<div class="bottom" style="position:absolute;left:0;width:1200px">© 2018 Company Name &nbsp;|&nbsp; All Rights Reserved</div>

</body>
</html>
```